TA BRAMLEY BUSINESS CARD DESIGN PROJECT

We need to utilize our logo that was expertly created on PixelHarbor and now need to match this with a business card design.

```html
<!DOCTYPE html>
<html lang="en">
<head>
<meta charset="utf-8">
<title>TA BRAMLEY Business Card</title>
<link href="https://fonts.googleapis.com/css2?family=Open+Sans:wght@400;600;700&display=swap" rel="stylesheet">
<style>
  :root {
    --brand-blue: #1558a7;
    --paper: #ffffff;
    --ink: #1a1a1a;
    --backdrop: #232323;
  }
  * { box-sizing: border-box; margin: 0; padding: 0; }
  html, body {
    width: 1200px; height: 780px; overflow: hidden;
    background: var(--backdrop);
    font-family: "Open Sans", Arial, sans-serif;
  }
  .canvas {
    position: relative; width: 1200px; height: 780px;
    display: flex; align-items: center; justify-content: center; gap: 40px;
  }
  .card {
    position: relative; width: 540px; height: 309px; overflow: hidden;
  }
  .card-front {
    background: var(--brand-blue);
    display: flex; align-items: center; justify-content: center;
  }
  .card-front .wordmark {
    color: var(--paper); font-weight: 700; font-size: 46px; letter-spacing: 4px;
  }
  .card-back { background: var(--paper); }
  .edge-bar {
    position: absolute; width: 11px; background: var(--brand-blue);
  }
  .edge-bar-left { left: 0; top: 22%; height: 53%; }
  .edge-bar-right { right: 0; top: 15%; height: 55%; }
  .back-logo {
    position: absolute; left: 40px; top: 100px; width: 200px;
    text-align: center;
    color: var(--brand-blue); font-weight: 700; font-size: 30px; letter-spacing: 2px;
  }
  .divider {
    position: absolute; left: 262px; top: 40px; width: 1px; height: 195px;
    background: var(--ink);
  }
  .contact {
    position: absolute; left: 285px; top: 42px; right: 20px;
  }
  .person-name {
    color: var(--brand-blue); font-weight: 700; font-size: 27px; line-height: 1.1;
  }
  .person-title {
    color: var(--ink); font-weight: 600; font-size: 14px; margin: 2px 0 14px 8px;
  }
  .contact-list { list-style: none; }
  .contact-list li {
    display: flex; align-items: center; gap: 8px;
    font-size: 13.5px; color: var(--ink); line-height: 1.55;
  }
  .contact-list .label { color: var(--brand-blue); }
  .contact-list svg { width: 13px; height: 13px; flex: none; }
  .address {
    position: absolute; left: 0; right: 0; bottom: 34px;
    text-align: center; font-size: 15px; color: var(--ink); padding-left: 80px;
  }
</style>
</head>
<body>
<main class="canvas">
  <section class="card card-front" aria-label="Card front">
    <span class="wordmark">TA BRAMLEY</span>
  </section>

  <section class="card card-back" aria-label="Card back">
    <div class="edge-bar edge-bar-left"></div>
    <div class="edge-bar edge-bar-right"></div>

    <div class="back-logo">TA BRAMLEY</div>
    <div class="divider"></div>

    <div class="contact">
      <h1 class="person-name">Dana M. Kessler</h1>
      <p class="person-title">Owner</p>
      <ul class="contact-list">
        <li>
          <svg viewBox="0 0 16 16" aria-hidden="true"><rect x="4" y="1" width="8" height="14" rx="1.5" fill="none" stroke="#1558a7" stroke-width="1.5"/></svg>
          <span>555-201-3344 <span class="label">(cell)</span></span>
        </li>
        <li>
          <svg viewBox="0 0 16 16" aria-hidden="true"><path d="M3 2 L6 2 L7 5 L5 6.5 Q6.5 9.5 9.5 11 L11 9 L14 10 L14 13 Q8 14 4 9 Q2 6 3 2 Z" fill="#1558a7"/></svg>
          <span>555-201-7788 <span class="label">(office)</span></span>
        </li>
        <li>
          <svg viewBox="0 0 16 16" aria-hidden="true"><circle cx="8" cy="8" r="6.5" fill="none" stroke="#1558a7" stroke-width="1.5"/><path d="M1.5 8 H14.5 M8 1.5 Q4 8 8 14.5 M8 1.5 Q12 8 8 14.5" fill="none" stroke="#1558a7" stroke-width="1.2"/></svg>
          <span>www.tabramley.com</span>
        </li>
        <li>
          <svg viewBox="0 0 16 16" aria-hidden="true"><rect x="1.5" y="3.5" width="13" height="9" fill="none" stroke="#1558a7" stroke-width="1.5"/><path d="M1.5 3.5 L8 9 L14.5 3.5" fill="none" stroke="#1558a7" stroke-width="1.5"/></svg>
          <span>dana@tabramley.com</span>
        </li>
      </ul>
    </div>

    <p class="address">240 Maple Ridge Rd Cedar Falls, WI 53000</p>
  </section>
</main>
</body>
</html>
```